Wordpress Business Travel Blog and Discussion Board

Oh, Hello!

We are looking for a motivated designer to create a full, turnkey interactive WordPress website geared toward business travel that includes a news style blog (look at ByteHarbor.com and Wirevane.com for the style we like) that is seamlessly integrated with a robust message board (look at GateBanter.com and RoamLedger.com). Ok, so stick with us here because this is actually a pretty cool project that shouldn't be too hard, but yes, of course we have some curve balls that we are throwing your way. Sorry! :)

*On the front page*

- We would like to have a typical news style blog layout that is fun, somewhat professional, and easy to read. That's easy!

- Somewhere within first glance, we would like to have a short list of the most active discussions on our discussion board. (What's trending, or something like that). Not too bad, right?

- Overall, want to have a good amount of content, but we also do not want the visitor to feel as if he or she is having to sift through a lot of content to see what he or she wants to see. Great! We're past the beginning!

We will have traditional visual advertising on all of our pages. Please leave space as necessary :)

*On the Blog/News story pages*

Let's keep these simple - but there is a twist!

Let's say I create a blog/news post. I would like that blog/news post to also be opened as a discussion on the discussion board. For example, I write an article about Coastal Skyways and their service on a particular international flight. This will be opened as a discussion under the Coastal Skyways topic in the discussion board. Other users can also open new discussions under any topic on the discussion board, but they cannot post stories (unless permission is given) to the blog wall. We would like their posts to show up as regular discussion board posts while the news/blog posts by us show up as news/blog posts on the front page, *and* (oh yes we did!) as discussions in the discussion board. Of course, users will still be able to post comments to the news/blog post, which will also be posted in the discussion.

OK, does that make sense? Let me know if I can help make this more clear! :) Sorry!

*Wiki Pages*

Take a look at the Coastal Skyways example above. In that example, my news/blog entry automatically opens a new discussion post. Although we won't necessarily need to create a new wiki page, we would like to tag the post and the discussion to a wiki page about the topic. The wiki page can be created and edited by all users (and locked by us if necessary). BONUS! Can we tag more than one wiki page?

*Websites that inspire us*

ByteHarbor.com - concept and design
Wirevane.com - concept and design
GateBanter.com - concept
RoamLedger.com - concept
pomwhispers.com - concept

All of the sites above are great and we can only thrive with their great success. We are not aiming to be a competitor to the travel sites, but just another great option for interested visitors. Please do not simply copy what they have. What is posted above is a list of our favorite sites that we visit every day.

Our favorite font is Segoe UI, but please don't use this (or a similar font) too much! Maybe just titles would be great. You're the designer so you can make the call here.

Also, our favorite color is blue, but if you have another favorite color, go ahead and show us what you can do! (Don't use too much blue!)

*Oh, and One More Thing*

(I know, you thought we were done. We're not!)

Here's the killer - We would like to create a way for people to, say, enter the details of their next trip and be matched with someone who will also be on a portion of their trip.

For example, let's say I am flying Meridian Airways flight 109 from Los Angeles to New York JFK Airport this Friday. I am staying at the Bellcourt New York Times Square on Friday night, and I am flying back on Saturday night on Kestrel flight 290 from New York JFK airport back to Los Angeles. Another user will also be on the Kestrel flight back to Los Angeles with me and he entered that information in the website. (Note, the user has to manually enter this information). The other user and I will both be notified that there is at least one other user who will be on the same Kestrel flight as me. We will both have the option to reveal our online identity - which will in fact be released to each person as long as each person *mutually* agrees.

This can be very simple - almost like a dating site type of match but it is based on two people being in the same place at the same time (based on what they report). Also, we would like to be able to collect this information - not necessarily tied to the user's true identity. The information we would like to have is - what the user is claiming he or she is doing on the trip (i.e. staying at the Bellcourt Times Square, flying Meridian Airways), and whether or not the user agreed to reveal his or her identity - AND! whether or not the users both revealed their identity.

*Most Important*

HAVE FUN and THANK YOU!! :)

A couple of quick notes - this is a design and code project. We are most likely offering a more $(!) design and code project for the version 2.0 of this website once we get user feedback from this first round.

Also, the name of the website is Jaunta. (www.jaunta-example.com)

Good luck!

Reason: Extending as requested by a few designers. Only 3 more days to get your designs in!

Reason: All designs look great! Last chance for one or two more designers who have requested an extension. All designs that were already submitted on time will be considered with much higher priority. Thank you!

Requirements
Must have
• We need to have a high end, professional, modern, and clean design on the front page to entice readers to constantly visit and stay on our site.
Nice to have
• It would be great to give us the ability to automatically recognize users for visiting the website and/or participating and commenting. Social badges, recognition, etc. would be very cool.
Should not have
• Although this is a website around business travel, we do not necessarily want it to be business travel themed. There can be hints of the theme, but otherwise the visual look should be somewhat generic.

```html
<!DOCTYPE html>
<html lang="en">
<head>
<meta charset="utf-8">
<title>Tidewell Travels</title>
<link href="https://fonts.googleapis.com/css2?family=Oswald:wght@400;500&family=Arimo:wght@400;700&display=swap" rel="stylesheet">
<style>
:root{
  --orange:#fbb02d;
  --orange-deep:#f39c12;
  --page:#eceeee;
  --panel:#efefef;
  --ink:#222;
  --muted:#6b6b6b;
  --rule:#cfcfcf;
  --night:#111;
  --white:#fff;
  --ad:#dcdfdf;
}
*{margin:0;padding:0;box-sizing:border-box}
html,body{width:984px;height:1200px;overflow:hidden}
body{position:relative;background:var(--page);font-family:"Arimo",Arial,sans-serif;color:var(--ink);border-top:4px solid var(--night)}
.abs{position:absolute}

/* header */
.account-tab{left:664px;top:0;width:258px;height:21px;background:var(--orange);clip-path:polygon(0 0,100% 0,92% 100%,8% 100%);display:flex;justify-content:center;gap:24px;align-items:center}
.account-tab a{font-family:"Oswald",sans-serif;font-size:11px;color:var(--night);text-decoration:none}
.brand{left:84px;top:18px;font-family:"Oswald",sans-serif;font-size:40px;line-height:50px;color:var(--orange);font-weight:500;letter-spacing:-.5px}
.search{left:720px;top:32px;width:159px;height:17px;background:var(--white);border:1px solid #ddd;border-radius:2px;font-size:10px;color:#555;padding:2px 5px}
.search svg{position:absolute;right:5px;top:2px}
.ad-slot{background:var(--ad);border:1px dashed #b9bdbd;display:flex;align-items:center;justify-content:center;font-family:"Oswald",sans-serif;font-size:10px;color:#8a8f8f;letter-spacing:1px}
.header-ad{left:350px;top:26px;width:340px;height:56px}

/* nav */
.main-nav{left:85px;top:99px;width:820px;height:40px;background:linear-gradient(#fcbd49,var(--orange-deep));border-radius:5px 5px 0 0;display:flex;align-items:center;padding-left:82px}
.main-nav a{font-family:"Oswald",sans-serif;font-size:13px;color:var(--night);text-decoration:none;text-transform:uppercase}

/* hero */
.hero{left:85px;top:139px;width:820px;height:306px;background:linear-gradient(180deg,#c9dbe6 0%,#7fb2c1 28%,#e9eef0 52%,#d7d0c3 80%,#bfae95 100%)}
.hero-caption{left:85px;top:390px;width:820px;height:55px;background:rgba(70,70,70,.72);color:var(--white);padding:6px 10px}
.hero-caption h1{font-family:"Oswald",sans-serif;font-weight:500;font-size:26px;line-height:28px;letter-spacing:-.8px}
.hero-caption p{font-family:"Oswald",sans-serif;font-size:10px;letter-spacing:-.3px}
.hero-dots{right:94px;top:419px;display:flex;gap:6px}
.hero-dots span{width:15px;height:14px;background:#eee;color:var(--night);font-family:"Oswald",sans-serif;font-size:10px;display:flex;align-items:center;justify-content:center;border-radius:2px}
.hero-arrow{top:251px;width:22px;height:23px;background:#f4f4f4;display:flex;align-items:center;justify-content:center}
.hero-shadow{left:120px;top:445px;width:770px;height:26px;background:radial-gradient(ellipse at top,rgba(0,0,0,.35),rgba(0,0,0,0) 70%)}

/* content */
.content{left:85px;top:471px;width:820px;height:521px;background:var(--white)}
.trending{left:95px;top:476px;width:789px;height:18px;display:flex;align-items:center;gap:10px;font-size:9.5px;color:#444;white-space:nowrap;overflow:hidden}
.trending strong{font-family:"Oswald",sans-serif;font-weight:400;font-size:10px;background:var(--orange);color:var(--night);padding:1px 6px;border-radius:2px}
.trending span + span::before{content:"•";color:var(--orange-deep);margin-right:10px}
.post{left:95px;width:486px}
.post h2{font-family:"Oswald",sans-serif;font-weight:400;font-size:14px;color:var(--night);letter-spacing:-.4px}
.post time{display:block;font-size:10px;color:var(--muted);margin-top:1px}
.post-photo{position:absolute;left:0;top:36px;width:138px;height:92px;background:linear-gradient(180deg,#5a9ad6 0%,#9fc4e2 40%,#c98c5c 55%,#2f6fb0 70%,#1b4d8c 100%)}
.post p{position:absolute;left:151px;top:36px;width:330px;font-size:10px;line-height:12px;color:#555;text-align:justify}
.read-more{position:absolute;left:417px;top:112px;width:62px;height:17px;background:#ddd;border-radius:2px;font-family:"Oswald",sans-serif;font-size:10px;color:#444;display:flex;align-items:center;justify-content:center}
.post-rule{position:absolute;left:0;top:144px;width:486px;height:1px;background:var(--rule)}
.column-rule{left:95px;top:497px;width:490px;height:2px;background:#e3e3e3}
.sidebar-rule{left:636px;top:497px;width:2px;height:478px;background:linear-gradient(#eee,#f7f7f7)}

/* sidebar */
.widget{left:654px;width:230px;background:var(--panel);border-radius:3px}
.widget h3{font-family:"Oswald",sans-serif;font-weight:400;font-size:15px;color:#444;text-align:center;padding-top:4px;letter-spacing:-.3px}
.widget .tag{position:absolute;left:17px;top:2px}
.newsletter-input{position:absolute;left:26px;top:39px;width:182px;height:21px;background:var(--white);border:1px solid #aaa;border-radius:4px}
.subscribe-btn{position:absolute;left:85px;top:67px;width:69px;height:21px;background:var(--orange);border-radius:3px;color:var(--white);font-family:"Oswald",sans-serif;font-size:14px;display:flex;align-items:center;justify-content:center}
.tweet-list{position:absolute;left:14px;top:32px;width:192px;list-style:none}
.tweet-list li{font-size:9.5px;line-height:12px;padding:1px 0 4px;border-bottom:1px solid var(--rule);margin-bottom:3px}
.tweet-list li:last-child{border:0;margin:0}
.article-list{position:absolute;left:17px;top:34px;width:195px;list-style:none}
.article-list li{font-family:"Oswald",sans-serif;font-size:11px;color:#333;height:22.5px;border-bottom:1px solid var(--rule);padding-top:4px;letter-spacing:-.4px}
.article-list li:last-child{border:0}
.article-list b{color:var(--orange-deep);font-weight:400;display:inline-block;width:15px;padding-left:6px}

/* footer */
.site-footer{left:0;top:992px;width:984px;height:185px;background:var(--orange);border-top:3px solid #d9d9d9}
.footer-col{top:1003px}
.footer-col h4{font-family:"Oswald",sans-serif;font-weight:400;font-size:18px;color:var(--night);letter-spacing:-.4px}
.follow-list{list-style:none;margin-top:8px}
.follow-list li{display:flex;align-items:center;gap:6px;font-size:9.5px;height:28px}
.follow-list i{width:22px;height:22px;border:2px solid var(--night);border-radius:50%;display:block;background:radial-gradient(circle,var(--night) 0 5px,transparent 5.5px)}
.footer-tweet{font-size:9.5px;line-height:12px;width:160px;margin-top:2px}
.footer-tweet .handle,.footer-tweet .ago{color:#fff}
.footer-tweet + .footer-tweet{border-top:1px solid #9a6a10;padding-top:8px;margin-top:8px}
.quick-links{list-style:none;margin-top:8px}
.quick-links li{font-size:9px;height:18px;padding-left:12px;position:relative}
.quick-links li::before{content:"";position:absolute;left:2px;top:4px;width:3px;height:3px;background:#fff;border-radius:50%}
.about-text{width:228px;font-size:9.5px;line-height:15px;text-align:justify;margin-top:4px}
.footer-brand{left:666px;top:1120px;font-family:"Oswald",sans-serif;font-size:26px;color:var(--white);font-weight:500}
.copyright{left:0;top:1177px;width:984px;height:23px;background:var(--night);color:var(--white);font-size:9px;text-align:right;padding:6px 80px 0 0}
</style>
</head>
<body>

<nav class="account-tab abs"><a>SIGNIN</a><a>REGISTER</a><a>HELP</a><a>FAQ</a></nav>
<div class="brand abs">Tidewell Travels</div>
<aside class="ad-slot header-ad abs">ADVERTISEMENT</aside>
<div class="search abs">Search
  <svg width="11" height="11" viewBox="0 0 11 11"><circle cx="4.5" cy="4.5" r="3.5" fill="none" stroke="#444" stroke-width="1.3"/><line x1="7" y1="7" x2="10.5" y2="10.5" stroke="#444" stroke-width="1.4"/></svg>
</div>

<div class="hero abs" role="img" aria-label="Family of three holding hands and playing in the surf on a sunny beach"></div>
<div class="hero-shadow abs"></div>
<nav class="main-nav abs">
  <a style="margin-right:52px">Home</a><a style="margin-right:48px">About</a><a style="margin-right:44px">Blog</a><a style="margin-right:52px">Forums</a><a style="margin-right:52px">Cities</a><a style="margin-right:47px">Services</a><a style="margin-right:50px">Testimonials</a><a>Contact</a>
</nav>
<div class="hero-arrow abs" style="left:85px"><svg width="8" height="12"><polyline points="6,1 1,6 6,11" fill="none" stroke="#f39c12" stroke-width="1.6"/></svg></div>
<div class="hero-arrow abs" style="left:883px"><svg width="8" height="12"><polyline points="2,1 7,6 2,11" fill="none" stroke="#f39c12" stroke-width="1.6"/></svg></div>
<div class="hero-caption abs">
  <h1>PHUKET’S MOST PRESTIGIOUS BOATING FACILITY</h1>
  <p>IS ALREADY DOUBLE THE SIZE OF ANY OTHER YACHTING MARINA ON THAILAND’S WORLD FAMOUS HOLIDAY ISLAND.</p>
</div>
<div class="hero-dots abs"><span>1</span><span>2</span><span>3</span><span>4</span><span>5</span></div>

<main class="content abs"></main>
<div class="trending abs">
  <strong>TRENDING DISCUSSIONS</strong>
  <span>Best lounges at JFK</span><span>Carry-on only for a week?</span><span>Points vs. cash upgrades</span><span>Quiet hotels near Times Square</span>
</div>
<div class="column-rule abs"></div>
<div class="sidebar-rule abs"></div>

<article class="post abs" style="top:507px">
  <h2>ORCHID BREEZE PHUKET FLIGHTS BEGIN OCT 1</h2><time>September 2, 2012</time>
  <div class="post-photo" role="img" aria-label="Resort hotel beside an infinity pool at dusk"></div>
  <p>Orchid Breeze, the new “light” airline launched by Lotus Air International, will begin direct flights from Phuket to Bangkok and Chiang Mai on October 1, it was announced yesterday.Orchid Breeze, the new “light” airline launched by Lotus Air International, will begin direct flights from Phuket to Bangkok and Chiang Mai on October 1, it was announced yesterday.will begin direct flights from Phuket to Bangkok .</p>
  <span class="read-more">READ MORE</span><span class="post-rule"></span>
</article>
<article class="post abs" style="top:662px">
  <h2>ORCHID BREEZE PHUKET FLIGHTS BEGIN OCT 1</h2><time>September 2, 2012</time>
  <div class="post-photo" role="img" aria-label="Resort hotel beside an infinity pool at dusk"></div>
  <p>Orchid Breeze, the new “light” airline launched by Lotus Air International, will begin direct flights from Phuket to Bangkok and Chiang Mai on October 1, it was announced yesterday.Orchid Breeze, the new “light” airline launched by Lotus Air International, will begin direct flights from Phuket to Bangkok and Chiang Mai on October 1, it was announced yesterday.will begin direct flights from Phuket to Bangkok .</p>
  <span class="read-more">READ MORE</span><span class="post-rule"></span>
</article>
<article class="post abs" style="top:813px">
  <h2>ORCHID BREEZE PHUKET FLIGHTS BEGIN OCT 1</h2><time>September 2, 2012</time>
  <div class="post-photo" role="img" aria-label="Resort hotel beside an infinity pool at dusk"></div>
  <p>Orchid Breeze, the new “light” airline launched by Lotus Air International, will begin direct flights from Phuket to Bangkok and Chiang Mai on October 1, it was announced yesterday.Orchid Breeze, the new “light” airline launched by Lotus Air International, will begin direct flights from Phuket to Bangkok and Chiang Mai on October 1, it was announced yesterday.will begin direct flights from Phuket to Bangkok .</p>
  <span class="read-more">READ MORE</span>
</article>

<section class="widget abs" style="top:513px;height:96px">
  <svg class="tag" width="13" height="19"><path d="M0 0H13V14L6.5 19L0 14Z" fill="#f39c12"/></svg>
  <h3>SUBSCRIBE FOR NEWLETTER</h3>
  <div class="newsletter-input"></div>
  <div class="subscribe-btn">SUBSCRIBE</div>
</section>
<section class="widget abs" style="top:622px;height:169px">
  <svg class="tag" width="13" height="19"><path d="M0 0H13V14L6.5 19L0 14Z" fill="#f39c12"/></svg>
  <h3>TOP &nbsp;TWEETS</h3>
  <ul class="tweet-list">
    <li>@Skyquill<br>Lorem ipsum dolor sit amet, consect</li>
    <li>@Skyquill<br>Lorem ipsum dolor sit amet, consect</li>
    <li>@Skyquill<br>Lorem ipsum dolor sit amet, consect</li>
    <li>@Skyquill<br>Lorem ipsum dolor sit amet, consect</li>
  </ul>
</section>
<section class="widget abs" style="top:804px;height:169px">
  <svg class="tag" width="13" height="19"><path d="M0 0H13V14L6.5 19L0 14Z" fill="#f39c12"/></svg>
  <h3>RECENT ARTICLES</h3>
  <ol class="article-list">
    <li><b>1</b>LOS VEGAS VACATION IDEAS</li>
    <li><b>2</b>BUDGET TRAVELLING</li>
    <li><b>3</b>THINGS TO DO IN EUROPE</li>
    <li><b>4</b>ANCIENT ROME - VISIT TODAY</li>
    <li><b>5</b>ANCIENT ROME - VISIT TODAY</li>
  </ol>
</section>

<footer class="site-footer abs"></footer>
<div class="footer-col abs" style="left:87px">
  <h4>Follow &nbsp;Us</h4>
  <ul class="follow-list">
    <li><i></i>Follow us on Facepage</li>
    <li><i></i>Follow us on Chirper</li>
    <li><i></i>Connect on Linkwork</li>
    <li><i></i>Follow our Rss</li>
    <li><i></i>Follow us on Facepage</li>
  </ul>
</div>
<div class="footer-col abs" style="left:296px">
  <h4>Recent Tweets</h4>
  <div class="footer-tweet"><span class="handle">@Skyquill</span><br>Lorem ipsum dolor sit amet, consect aretuer adipiscing elit. Praesent ves tibulum molestie cus.<br><span class="ago">About 2 Hours ago</span></div>
  <div class="footer-tweet"><span class="handle">@Skyquill</span><br>Lorem ipsum dolor sit amet, consect aretuer adipiscing elit. Praesent ves tibulum molestie cus.<br><span class="ago">About 2 Hours ago</span></div>
</div>
<div class="footer-col abs" style="left:530px">
  <h4>Quick Links</h4>
  <ul class="quick-links">
    <li>Home</li><li>About Us</li><li>Blog</li><li>Forums</li><li>Services</li><li>Cities</li><li>Testimonials</li><li>Contact Us</li>
  </ul>
</div>
<div class="footer-col abs" style="left:669px">
  <h4>About Tidewell Travels</h4>
  <p class="about-text">Lorem ipsum dolor sit amet, consect aretuer adipiscing elit. Praesent ves tibulum molestie cus. Aeneannonummy ret mauris. Phasellus porta. Fusce scit varius mi. Cum sociis natoque penatis et magnis dis parturient montes nascetur ridiculus mus. Nulla...</p>
</div>
<div class="footer-brand abs">Tidewell Travels</div>
<div class="copyright abs">COPYRIGHT @ TIDEWELLTRAVELS.EXAMPLE</div>

</body>
</html>
```